RTavenor Business Cards & Letterhead

I have a logo but need a design for some new business cards. We are a Design-Build Firm that specializes in the design and construction of commercial projects.
the cards need to be professional. no cartoon stuff.
i would like to have the cards in AI format so I can update the card as needed. Logo is provided.
Our Address is: 4187 Marlowe Ct. Linwood, South Dakota 27614

```html
<!DOCTYPE html>
<html lang="en">
<head>
<meta charset="UTF-8">
<title>RTavenor Business Cards</title>
<link href="https://fonts.googleapis.com/css2?family=Open+Sans:wght@400;600;700;800&display=swap" rel="stylesheet">
<style>
  :root {
    --backdrop: #333333;
    --card: #202024;
    --brand-blue: #1578bd;
    --wordmark-grey: #77787c;
    --text-light: #f2f2f2;
    --rule: #bfc3c8;
  }
  * { box-sizing: border-box; margin: 0; padding: 0; }
  html, body {
    width: 1200px;
    height: 780px;
    overflow: hidden;
    background: var(--backdrop);
    font-family: "Open Sans", Arial, sans-serif;
  }
  .sheet {
    width: 1200px;
    height: 780px;
    display: flex;
    align-items: center;
    justify-content: center;
    gap: 40px;
  }
  .card {
    width: 540px;
    height: 309px;
    background: var(--card);
    position: relative;
    box-shadow: 0 10px 24px rgba(0,0,0,0.45);
  }

  /* Back of card: wordmark */
  .card-back {
    display: flex;
    align-items: center;
    justify-content: center;
  }
  .back-wordmark {
    display: flex;
    align-items: center;
    gap: 12px;
  }
  .back-wordmark .mark-square {
    width: 30px;
    height: 30px;
    background: var(--brand-blue);
  }
  .back-wordmark .mark-name {
    font-weight: 800;
    font-size: 44px;
    letter-spacing: 1px;
    color: var(--wordmark-grey);
    text-transform: uppercase;
  }

  /* Front of card: contact details */
  .card-front .front-wordmark {
    position: absolute;
    left: 30px;
    top: 0;
    width: 240px;
    height: 309px;
    display: flex;
    align-items: center;
    justify-content: center;
    gap: 10px;
  }
  .front-wordmark .mark-square {
    width: 22px;
    height: 22px;
    background: var(--brand-blue);
  }
  .front-wordmark .mark-name {
    font-weight: 800;
    font-size: 30px;
    color: var(--brand-blue);
    text-transform: uppercase;
  }
  .divider {
    position: absolute;
    left: 290px;
    top: 68px;
    width: 1px;
    height: 174px;
    background: var(--rule);
  }
  .details {
    position: absolute;
    left: 310px;
    top: 70px;
    width: 215px;
    color: var(--text-light);
  }
  .person-name {
    font-weight: 800;
    font-size: 19px;
    color: var(--brand-blue);
    letter-spacing: 0.5px;
    line-height: 1.1;
    white-space: nowrap;
  }
  .person-title {
    font-weight: 700;
    font-size: 12.5px;
    margin-top: 3px;
  }
  .address {
    font-size: 12.5px;
    line-height: 1.4;
    margin-top: 12px;
  }
  .contact-list {
    list-style: none;
    margin-top: 12px;
    font-size: 12.5px;
    line-height: 1.45;
  }
  .contact-list li {
    display: flex;
    align-items: center;
    gap: 7px;
    white-space: nowrap;
  }
  .contact-list svg {
    width: 11px;
    height: 11px;
    fill: var(--brand-blue);
    flex: none;
  }
</style>
</head>
<body>
<main class="sheet">

  <section class="card card-back" aria-label="Card back">
    <div class="back-wordmark">
      <span class="mark-square"></span>
      <span class="mark-name">RTavenor</span>
    </div>
  </section>

  <section class="card card-front" aria-label="Card front">
    <div class="front-wordmark">
      <span class="mark-square"></span>
      <span class="mark-name">RTavenor</span>
    </div>
    <div class="divider"></div>
    <div class="details">
      <h1 class="person-name">ROWAN TAVENOR</h1>
      <p class="person-title">Founder/President</p>
      <p class="address">4187 Marlowe Ct. Linwood,<br>South Dakota 27614</p>
      <ul class="contact-list">
        <li>
          <svg viewBox="0 0 24 24" aria-hidden="true"><path d="M6.6 10.8a15.1 15.1 0 0 0 6.6 6.6l2.2-2.2c.3-.3.7-.4 1-.2 1.1.4 2.3.6 3.6.6.6 0 1 .4 1 1V20c0 .6-.4 1-1 1A17 17 0 0 1 3 4c0-.6.4-1 1-1h3.5c.6 0 1 .4 1 1 0 1.3.2 2.5.6 3.6.1.3 0 .7-.2 1z"/></svg>
          (555) 304-0148
        </li>
        <li>
          <svg viewBox="0 0 24 24" aria-hidden="true"><path d="M12 2a10 10 0 1 0 0 20 10 10 0 0 0 0-20zm6.9 6h-3a15.7 15.7 0 0 0-1.3-3.6A8 8 0 0 1 18.9 8zM12 4c.8 1.2 1.5 2.5 1.9 4h-3.8c.4-1.5 1.1-2.8 1.9-4zM4.3 14a8 8 0 0 1 0-4h3.4a16.5 16.5 0 0 0 0 4H4.3zm.8 2h3a15.7 15.7 0 0 0 1.3 3.6A8 8 0 0 1 5.1 16zm3-8h-3a8 8 0 0 1 4.3-3.6C8.8 5.5 8.4 6.7 8.1 8zM12 20c-.8-1.2-1.5-2.5-1.9-4h3.8c-.4 1.5-1.1 2.8-1.9 4zm2.3-6H9.7a14.7 14.7 0 0 1 0-4h4.6a14.7 14.7 0 0 1 0 4zm.3 5.6c.6-1.1 1-2.3 1.3-3.6h3a8 8 0 0 1-4.3 3.6zM16.3 14a16.5 16.5 0 0 0 0-4h3.4a8 8 0 0 1 0 4h-3.4z"/></svg>
          www.rtavenor.com
        </li>
        <li>
          <svg viewBox="0 0 24 24" aria-hidden="true"><path d="M2 5h20v14H2V5zm2 2v.5l8 5 8-5V7H4zm16 2.8-8 5-8-5V17h16V9.8z"/></svg>
          RT@RTavenor.com
        </li>
      </ul>
    </div>
  </section>

</main>
</body>
</html>
```